Oil Field Service company needs professional business cards

Looking to clean up our current company business cards and look a little more professional. Brenwick Casing Services is a US based company that services the oil field. We deal with engineers, managers and oil rigs....................................................................................................................................................................................................................................................................................................................................................................................................

Target Market(s)

Oil and Gas professionals

Industry/Entity Type

Oil And Gas

Contact Information for Business Card

See attached photo as example

Font styles to use
Sans Serif

Colors
ec1f27

Requirements
Must have
• Company Logo, Name, Title, Cell, Office, Fax, Email.
• See attached photo
Nice to have
• External CRT, Internal CRT, Casing Crews, Torque Turn, Laydown Machine
Should not have
• Do not introduce any new pictures and keep it professional looking

```html
<!DOCTYPE html>
<html lang="en">
<head>
<meta charset="utf-8">
<title>Brenwick Casing Services – Business Card</title>
<link rel="stylesheet" href="https://fonts.googleapis.com/css2?family=Archivo:wght@800&family=Roboto:wght@400&family=Roboto+Condensed:wght@400&display=swap">
<style>
  :root {
    --brand-red: #d42020;
    --accent-red: #ec1f27;
    --slate: #3b4754;
    --ink: #2e2e30;
    --muted: #555a60;
    --card-white: #fbfbfa;
    --backdrop: #e9e9e9;
  }
  * { margin: 0; padding: 0; box-sizing: border-box; }
  html, body {
    width: 1200px;
    height: 576px;
    overflow: hidden;
    background: var(--backdrop);
  }
  .stage { position: relative; width: 1200px; height: 576px; }

  .card {
    position: absolute;
    top: 139px;
    height: 293px;
    border-radius: 6px;
  }
  .card-front {
    left: 82px;
    width: 484px;
    background: var(--brand-red);
  }
  .card-back {
    left: 602px;
    width: 481px;
    background: var(--card-white);
    border: 1px solid #dcdcdc;
  }

  .wordmark {
    position: absolute;
    text-align: center;
    font-family: "Archivo", "Arial Black", sans-serif;
    font-weight: 800;
    line-height: 1;
  }
  .wordmark .wordmark-main { display: block; letter-spacing: 0.5px; }
  .wordmark .wordmark-sub { display: block; letter-spacing: 2px; }

  .card-front .wordmark {
    left: 0; right: 0; top: 112px;
    color: #ffffff;
  }
  .card-front .wordmark-main { font-size: 44px; }
  .card-front .wordmark-sub { font-size: 14px; margin-top: 14px; letter-spacing: 2.6px; }

  .card-back .wordmark {
    left: 264px; width: 200px; top: 206px;
    color: var(--slate);
  }
  .card-back .wordmark-main { font-size: 32px; }
  .card-back .wordmark-sub { font-size: 11px; margin-top: 10px; letter-spacing: 1.8px; }

  .holder { position: absolute; left: 23px; top: 44px; }
  .holder-name {
    font-family: "Archivo", "Arial Black", sans-serif;
    font-weight: 800;
    font-size: 21px;
    color: var(--ink);
    letter-spacing: 0.3px;
  }
  .holder-title {
    font-family: "Roboto", Arial, sans-serif;
    font-size: 11.5px;
    color: var(--muted);
    margin-top: 2px;
  }

  .contact-list {
    position: absolute;
    left: 26px;
    top: 307px;
    top: 168px;
    list-style: none;
    font-family: "Roboto Condensed", "Arial Narrow", sans-serif;
    font-size: 12px;
    color: var(--ink);
  }
  .contact-list li {
    display: flex;
    align-items: center;
    height: 16px;
  }
  .contact-icon {
    width: 10px;
    height: 10px;
    margin-right: 10px;
    fill: var(--accent-red);
    flex: none;
  }
  .web-highlight { color: var(--accent-red); }
</style>
</head>
<body>
<main class="stage">

  <section class="card card-front" aria-label="Card front">
    <div class="wordmark">
      <span class="wordmark-main">BRENWICK</span>
      <span class="wordmark-sub">CASING SERVICES</span>
    </div>
  </section>

  <section class="card card-back" aria-label="Card back">
    <div class="holder">
      <h1 class="holder-name">CODY HARLAN</h1>
      <p class="holder-title">Area Manager</p>
    </div>

    <ul class="contact-list">
      <li>
        <svg class="contact-icon" viewBox="0 0 10 10" aria-hidden="true"><path d="M2 0.5 L3.6 2.6 L2.7 3.6 C3.3 5 4.9 6.6 6.3 7.2 L7.3 6.3 L9.5 7.9 L8.4 9.5 C4.5 9.2 0.8 5.5 0.5 1.6 Z"/></svg>
        (580) 555-0142
      </li>
      <li>
        <svg class="contact-icon" viewBox="0 0 10 10" aria-hidden="true"><path d="M0.5 3.5 C2 1.5 8 1.5 9.5 3.5 L8.5 4.6 L7 3.8 L7 3 C5.8 2.7 4.2 2.7 3 3 L3 3.8 L1.5 4.6 Z M2.5 5 L7.5 5 L8.5 9 L1.5 9 Z"/></svg>
        (580) 555-0187
      </li>
      <li>
        <svg class="contact-icon" viewBox="0 0 10 10" aria-hidden="true"><path d="M2.5 0.5 H7.5 V3 H2.5 Z M0.5 3.5 H9.5 V7.5 H8 V6 H2 V7.5 H0.5 Z M2.5 6.5 H7.5 V9.5 H2.5 Z"/></svg>
        (580) 555-0163
      </li>
      <li>
        <svg class="contact-icon" viewBox="0 0 10 10" aria-hidden="true"><path d="M5 0.3 C2.9 0.3 1.5 1.9 1.5 3.8 C1.5 6.2 5 9.7 5 9.7 C5 9.7 8.5 6.2 8.5 3.8 C8.5 1.9 7.1 0.3 5 0.3 Z M5 2.5 A1.3 1.3 0 1 1 5 5.1 A1.3 1.3 0 1 1 5 2.5 Z" fill-rule="evenodd"/></svg>
        Redfield, OK 73000
      </li>
      <li>
        <svg class="contact-icon" viewBox="0 0 10 10" aria-hidden="true"><path d="M0.5 2 H9.5 L5 5.5 Z M0.5 3 L5 6.5 L9.5 3 V8 H0.5 Z"/></svg>
        codyharlan@brenwickcs.com
      </li>
      <li>
        <svg class="contact-icon" viewBox="0 0 10 10" aria-hidden="true"><path d="M5 0.5 A4.5 4.5 0 1 0 5 9.5 A4.5 4.5 0 1 0 5 0.5 Z M1.6 4.5 H3.3 C3.4 3.2 3.7 2 4.2 1.5 C2.8 1.8 1.8 3 1.6 4.5 Z M4.2 4.5 H5.8 C5.7 3.1 5.4 2 5 1.5 C4.6 2 4.3 3.1 4.2 4.5 Z M6.7 4.5 H8.4 C8.2 3 7.2 1.8 5.8 1.5 C6.3 2 6.6 3.2 6.7 4.5 Z M1.6 5.5 C1.8 7 2.8 8.2 4.2 8.5 C3.7 8 3.4 6.8 3.3 5.5 Z M4.2 5.5 C4.3 6.9 4.6 8 5 8.5 C5.4 8 5.7 6.9 5.8 5.5 Z M6.7 5.5 C6.6 6.8 6.3 8 5.8 8.5 C7.2 8.2 8.2 7 8.4 5.5 Z" fill-rule="evenodd"/></svg>
        <span>www.<span class="web-highlight">brenwickcs</span>.com</span>
      </li>
    </ul>

    <div class="wordmark">
      <span class="wordmark-main">BRENWICK</span>
      <span class="wordmark-sub">CASING SERVICES</span>
    </div>
  </section>

</main>
</body>
</html>
```